Refresh Brightpath Coursecraft

Need a new design for e-learning development and web app development site: http://brightpathcoursecraft.example. Need pages for everything on menu bar plus a training services and a web app development services pages and a better page for samples http://brightpathcoursecraft.example/samples5/.

***Must be programmed in html 5. NO CMS. No WP. No Plume. Straight html/css.

Target Market(s)

government

Industry/Entity Type

Government

Coding

Coded - Design and coding required

Number of Pages Required

1 page

Requirements
Must have
• Must be coded in html5/css. No CMS.
• Divided so you can easily see that we offer 3 separate services:
• Live Training - E-Learning Development - Web App Development
• A way to display logos of all our clients like on bottom of this page: https://www.quorvatests.example (this is also our website so you can copy all these logos)
• List both our Denver location which is already on our website plus our office in Velmoro Plaza. Street 62 Sur, 14-87. Medellín, Antioquia.
• A page like this for our web app dev services https://www.tekvanu.example/product-development
Should not have
• CMS

```html
<!DOCTYPE html>
<html lang="en">
<head>
<meta charset="utf-8">
<title>Brightpath Coursecraft — Instructional Design &amp; Courseware</title>
<link href="https://fonts.googleapis.com/css2?family=Raleway:wght@400;500;600;700&family=Montserrat:wght@400;500;600&display=swap" rel="stylesheet">
<style>
:root{
  --orange:#f7941d;
  --blue:#1b75bc;
  --sky:#3d9ad8;
  --ink:#222;
  --text:#3b3b3b;
  --grey-bg:#ececec;
  --footer:#1c1c1c;
  --footer-text:#e6e6e6;
  --white:#fff;
}
*{box-sizing:border-box;margin:0;padding:0}
html,body{width:1200px;height:3846px;overflow:hidden}
body{font-family:"Raleway",sans-serif;color:var(--text);background:var(--white);position:relative}
a{color:inherit;text-decoration:none}

/* header */
.site-header{position:absolute;top:0;left:0;width:1200px;height:154px;background:var(--white);z-index:3}
.brand{position:absolute;left:118px;top:40px;display:flex;align-items:center;gap:14px}
.brand-dot{width:64px;height:64px;border-radius:50%;background:var(--blue)}
.brand-name{font-family:"Raleway",sans-serif;font-weight:700;font-size:24px;line-height:1.1;color:var(--orange);width:180px}
.header-contact{position:absolute;top:30px;right:118px;display:flex;gap:46px;font-family:"Montserrat",sans-serif}
.contact-item{display:flex;align-items:center;gap:14px}
.contact-item svg{width:40px;height:34px}
.contact-item small{display:block;font-size:13px;color:var(--ink)}
.contact-item strong{display:block;font-size:14px;font-weight:600;color:var(--blue)}
.main-nav{position:absolute;top:94px;right:118px;display:flex;gap:54px;font-family:"Montserrat",sans-serif;font-size:19px;color:var(--ink)}

/* hero */
.hero{position:absolute;top:154px;left:0;width:1200px;height:580px;overflow:hidden}
.hero-photo{position:absolute;inset:0;background:linear-gradient(100deg,#f4f1ec 0%,#ede3d6 40%,#c9b59f 70%,#6d7b92 100%)}
.hero-copy{position:absolute;left:98px;top:118px}
.hero-brand{display:flex;align-items:center;gap:10px;margin-bottom:16px}
.hero-brand .brand-dot{width:44px;height:44px}
.hero-brand span{font-weight:700;font-size:20px;color:var(--orange)}
.hero-title{font-weight:500;font-size:41px;line-height:1.3;color:var(--ink);width:520px}
.btn{display:inline-flex;align-items:center;gap:10px;background:var(--orange);color:var(--white);font-family:"Montserrat",sans-serif;font-weight:600;font-size:15px;text-transform:uppercase;padding:0 24px;height:48px;box-shadow:0 3px 6px rgba(0,0,0,.18)}
.btn svg{width:16px;height:18px}
.hero .btn{margin-top:38px}
.hero-curve{position:absolute;left:0;bottom:0;width:1200px;height:120px}

/* intro */
.intro{position:absolute;top:734px;left:0;width:1200px;height:548px;text-align:center}
.intro-mark{width:78px;height:78px;border-radius:50%;background:var(--blue);margin:100px auto 0}
.intro h1{font-weight:700;font-size:33px;line-height:1.4;margin-top:16px}
.intro h1 .accent{color:var(--orange);display:block}
.intro h1 .main{color:var(--blue);display:block}
.intro p{width:890px;margin:24px auto 0;font-size:16.5px;line-height:29px;color:var(--ink)}
.intro .btn{margin-top:28px}

/* services */
.services{position:absolute;top:1282px;left:0;width:1200px;height:1456px;background:var(--grey-bg)}
.section-title{font-weight:600;font-size:32px;color:var(--orange);text-align:center;text-transform:uppercase}
.services .section-title{margin-top:108px}
.service{position:absolute;left:103px;width:994px;height:334px}
.service-photo{position:absolute;top:0;width:476px;height:334px;box-shadow:0 3px 8px rgba(0,0,0,.2)}
.service-photo::after{content:"";position:absolute;right:0;bottom:0;width:64px;height:64px;background:var(--white);border-top-left-radius:64px}
.service-photo i{position:absolute;right:12px;bottom:12px;width:30px;height:30px;border-radius:50%;background:var(--blue);z-index:1}
.service-body{position:absolute;top:36px;width:480px}
.service h2{font-weight:600;font-size:30px;color:var(--blue);text-transform:uppercase}
.service p{margin-top:10px;font-size:15.5px;line-height:29px;color:var(--ink)}
.service .btn{margin-top:24px;text-transform:none;font-size:14px;height:46px}
.service.photo-left .service-photo{left:0}
.service.photo-left .service-body{left:518px}
.service.photo-right .service-photo{left:517px}
.service.photo-right .service-body{left:0}
.svc-live{top:200px}
.svc-elearning{top:610px}
.svc-webapp{top:1015px}
.photo-live{background:linear-gradient(120deg,#d8d2c8,#f1e8dc 45%,#9fb6cc 100%)}
.photo-elearning{background:linear-gradient(135deg,#c79a6a,#e2bf94 50%,#b9855a)}
.photo-webapp{background:linear-gradient(120deg,#cfd6dc,#6d7784 50%,#2d3440)}

/* clients */
.clients{position:absolute;top:2738px;left:0;width:1200px;height:600px}
.clients .section-title{margin-top:98px}
.client-row{position:absolute;left:100px;width:1000px;display:flex;justify-content:space-between;align-items:center}
.client{display:flex;align-items:center;gap:6px;font-weight:600;font-size:15px;color:#5a5a5a}
.client b{width:20px;height:20px;border-radius:50%;background:#9a9a9a;flex:none}
.row-1{top:240px}.row-2{top:346px}.row-3{top:452px}

/* footer */
.site-footer{position:absolute;top:3333px;left:0;width:1200px;height:513px;overflow:hidden}
.footer-bg{position:absolute;inset:0;background:linear-gradient(180deg,#2a2a2a,#141414)}
.footer-curve{position:absolute;top:0;left:0;width:1200px;height:110px}
.footer-brand{position:absolute;left:108px;top:228px}
.footer-brand .brand-name{color:var(--white);font-size:20px;width:160px}
.footer-brand .brand-dot{width:50px;height:50px;background:var(--orange)}
.socials{display:flex;gap:10px;margin:16px 0 0 26px}
.socials span{width:26px;height:26px;border-radius:50%;background:var(--white)}
.footer-col{position:absolute;top:170px;color:var(--footer-text)}
.footer-col h3{font-weight:600;font-size:25px;color:var(--white);margin-bottom:26px}
.col-contact{left:362px;width:230px}
.col-links{left:615px}
.col-news{left:828px;width:282px}
.contact-line{display:flex;gap:18px;font-size:13.5px;line-height:24px;margin-bottom:16px}
.contact-line svg{width:16px;height:20px;flex:none;margin-top:2px}
.col-links li{list-style:none;font-size:13.5px;line-height:28px;display:flex;align-items:center;gap:16px}
.col-links li::before{content:"";width:8px;height:8px;border-radius:50%;background:var(--white)}
.col-news p{font-size:13.5px}
.email-field{margin-top:18px;width:282px;height:44px;background:var(--white);color:#777;font-size:13px;padding:0 16px;display:flex;align-items:center}
.subscribe{margin-top:18px;width:128px;height:42px;background:var(--blue);color:var(--white);font-weight:600;font-size:13px;display:flex;align-items:center;justify-content:center;text-transform:uppercase}
.footer-rule{position:absolute;left:0;top:442px;width:1200px;height:1px;background:rgba(255,255,255,.3)}
.copyright{position:absolute;top:462px;width:1200px;text-align:center;font-size:13.5px;color:var(--footer-text)}
</style>
</head>
<body>

<header class="site-header">
  <a class="brand" href="#"><span class="brand-dot"></span><span class="brand-name">Brightpath Coursecraft</span></a>
  <div class="header-contact">
    <div class="contact-item">
      <svg viewBox="0 0 40 30"><rect x="1" y="2" width="38" height="26" fill="var(--orange)"/><path d="M1 2 L20 17 L39 2" fill="none" stroke="#fff" stroke-width="2.5"/></svg>
      <div><small>Mail us on:</small><strong>INFO@BRIGHTPATHCOURSECRAFT.EXAMPLE</strong></div>
    </div>
    <div class="contact-item">
      <svg viewBox="0 0 34 34"><circle cx="17" cy="17" r="15" fill="none" stroke="var(--orange)" stroke-width="2.5"/><path d="M11 9 l4 0 l2 5 l-3 2 a10 10 0 0 0 5 5 l2 -3 l5 2 l0 4 a3 3 0 0 1 -3 2 a17 17 0 0 1 -15 -15 a3 3 0 0 1 3 -2z" fill="var(--orange)"/></svg>
      <div><small>Call us on:</small><strong>888-555-0147</strong></div>
    </div>
  </div>
  <nav class="main-nav"><a href="#">Home</a><a href="#">Portfolio</a><a href="#">Services</a><a href="#">Team &amp; Experience</a><a href="#">Contacts</a></nav>
</header>

<section class="hero">
  <div class="hero-photo" role="img" aria-label="Photo of learners working at laptops in a bright classroom"></div>
  <div class="hero-copy">
    <div class="hero-brand"><span class="brand-dot"></span><span>Brightpath Coursecraft</span></div>
    <h2 class="hero-title">We create engaging training that exceed expectations.</h2>
    <a class="btn" href="#"><svg viewBox="0 0 16 18"><path d="M1 1h9l5 5v11H1z" fill="#fff"/></svg>Read more</a>
  </div>
  <svg class="hero-curve" viewBox="0 0 1200 120" preserveAspectRatio="none">
    <path d="M0 40 Q600 150 1200 40 L1200 120 L0 120z" fill="#fff"/>
    <path d="M0 40 Q600 150 1200 40" fill="none" stroke="var(--blue)" stroke-width="6"/>
    <path d="M0 58 Q600 158 1200 58" fill="none" stroke="#b9d4ea" stroke-width="3"/>
  </svg>
</section>

<section class="intro">
  <div class="intro-mark"></div>
  <h1><span class="accent">INSTRUCTIONAL DESIGN AND COURSEWARE</span><span class="main">DEVELOPMENT FIRM</span></h1>
  <p>Brightpath Coursecraft is a HUBZone Certified, SBA 8(a) Certified, Native American Owned Small Disadvantaged Business located in Denver, Colorado. We have designed and delivered SCORM compliant eLearning, webinar, web-based training (WBT), instructor-led training (ILT), virtual ILT (vILT), blended, and 3D Immersive training courses.</p>
  <a class="btn" href="#"><svg viewBox="0 0 16 18"><path d="M1 1h9l5 5v11H1z" fill="#fff"/></svg>Read more</a>
</section>

<section class="services">
  <h2 class="section-title">Our Services</h2>

  <article class="service photo-left svc-live">
    <div class="service-photo photo-live" role="img" aria-label="Photo of a trainee with headphones taking notes at a desktop computer"><i></i></div>
    <div class="service-body">
      <h2>Live Training</h2>
      <p>Sed ut perspiciatis unde omnis iste natus error sit voluptatem accusantium doloremque laudantium, totam rem aperiam, eaque ipsa quae ab illo inventore veritatis et quasi architecto beatae vitae dicta sunt explicabo. sed quia consequuntur magni dolores eos qui ratione voluptatem sequi nesciunt.</p>
      <a class="btn" href="#"><svg viewBox="0 0 18 14"><rect x="3" y="1" width="12" height="9" fill="none" stroke="#fff" stroke-width="2"/><rect x="0" y="11" width="18" height="2" fill="#fff"/></svg>Read More</a>
    </div>
  </article>

  <article class="service photo-right svc-elearning">
    <div class="service-body">
      <h2>E-Learning Development</h2>
      <p>Sed ut perspiciatis unde omnis iste natus error sit voluptatem accusantium doloremque laudantium, totam rem aperiam, eaque ipsa quae ab illo inventore veritatis et quasi architecto beatae vitae dicta sunt explicabo. sed quia consequuntur magni dolores eos qui ratione voluptatem sequi nesciunt.</p>
      <a class="btn" href="#"><svg viewBox="0 0 18 14"><rect x="3" y="1" width="12" height="9" fill="none" stroke="#fff" stroke-width="2"/><rect x="0" y="11" width="18" height="2" fill="#fff"/></svg>Read More</a>
    </div>
    <div class="service-photo photo-elearning" role="img" aria-label="Photo of a laptop, tablet and notes on a wooden desk"><i></i></div>
  </article>

  <article class="service photo-left svc-webapp">
    <div class="service-photo photo-webapp" role="img" aria-label="Photo of developers reviewing code on monitors"><i></i></div>
    <div class="service-body">
      <h2>Web App Development</h2>
      <p>Sed ut perspiciatis unde omnis iste natus error sit voluptatem accusantium doloremque laudantium, totam rem aperiam, eaque ipsa quae ab illo inventore veritatis et quasi architecto beatae vitae dicta sunt explicabo. sed quia consequuntur magni dolores eos qui ratione voluptatem sequi nesciunt.</p>
      <a class="btn" href="#"><svg viewBox="0 0 18 14"><rect x="3" y="1" width="12" height="9" fill="none" stroke="#fff" stroke-width="2"/><rect x="0" y="11" width="18" height="2" fill="#fff"/></svg>Read More</a>
    </div>
  </article>
</section>

<section class="clients">
  <h2 class="section-title">A few of our 75,000 clients</h2>
  <div class="client-row row-1">
    <span class="client"><b></b>Northwind Corps</span>
    <span class="client"><b></b>Halvern</span>
    <span class="client"><b></b>Corvan</span>
    <span class="client"><b></b>Workbridge</span>
    <span class="client"><b></b>Pellam</span>
    <span class="client">Quillan</span>
    <span class="client"><b></b>Verdalis</span>
    <span class="client">Raskel</span>
  </div>
  <div class="client-row row-2">
    <span class="client"><b></b>Ostrey</span>
    <span class="client"><b></b>Ashmoor</span>
    <span class="client"><b></b>Keldon University</span>
    <span class="client"><b></b>Orvexa Labs</span>
    <span class="client"><b></b>Dunmere</span>
    <span class="client"><b></b>Fenwick</span>
  </div>
  <div class="client-row row-3">
    <span class="client"><b></b>Brisa</span>
    <span class="client">Marrow State</span>
    <span class="client">Tallis</span>
    <span class="client"><b></b>Galvey</span>
    <span class="client"><b></b>Torin</span>
    <span class="client"><b></b>Emberline</span>
    <span class="client"><b></b>Selby</span>
    <span class="client"><b></b>Olvaro</span>
  </div>
</section>

<footer class="site-footer">
  <div class="footer-bg" role="img" aria-label="Dimmed photo of people collaborating at a table"></div>
  <svg class="footer-curve" viewBox="0 0 1200 110" preserveAspectRatio="none">
    <path d="M0 0 L1200 0 L1200 50 Q600 -30 0 50z" fill="#fff"/>
    <path d="M0 50 Q600 -30 1200 50" fill="none" stroke="var(--blue)" stroke-width="7"/>
    <path d="M0 66 Q600 -14 1200 66" fill="none" stroke="#8fb8dc" stroke-width="3"/>
  </svg>

  <div class="footer-brand">
    <a class="brand" style="position:static" href="#"><span class="brand-dot"></span><span class="brand-name">Brightpath Coursecraft</span></a>
    <div class="socials"><span></span><span></span><span></span><span></span></div>
  </div>

  <div class="footer-col col-contact">
    <h3>Contact Us</h3>
    <div class="contact-line"><svg viewBox="0 0 16 20"><path d="M8 1a6 6 0 0 1 6 6c0 5-6 12-6 12S2 12 2 7a6 6 0 0 1 6-6z" fill="none" stroke="#fff" stroke-width="1.6"/><circle cx="8" cy="7" r="2" fill="#fff"/></svg><span>Street 62 Sur, 14-87,<br>Medellín, Antioquia</span></div>
    <div class="contact-line"><svg viewBox="0 0 16 20"><path d="M8 1a6 6 0 0 1 6 6c0 5-6 12-6 12S2 12 2 7a6 6 0 0 1 6-6z" fill="none" stroke="#fff" stroke-width="1.6"/><circle cx="8" cy="7" r="2" fill="#fff"/></svg><span>2750 Larkspur Avenue, Suite 2-118 Aurora, CO. 80011</span></div>
    <div class="contact-line"><svg viewBox="0 0 16 20"><path d="M3 3h3l1.5 4-2 1.5a8 8 0 0 0 4 4l1.5-2 4 1.5v3a2 2 0 0 1-2 2A13 13 0 0 1 1 5a2 2 0 0 1 2-2z" fill="none" stroke="#fff" stroke-width="1.6"/></svg><span>Phone: 888 555 0199</span></div>
    <div class="contact-line"><svg viewBox="0 0 16 20"><rect x="1" y="5" width="14" height="10" fill="none" stroke="#fff" stroke-width="1.6"/><path d="M1 5l7 6 7-6" fill="none" stroke="#fff" stroke-width="1.6"/></svg><span>info@brightpath.example</span></div>
  </div>

  <div class="footer-col col-links">
    <h3>Quick Links</h3>
    <ul><li>Home</li><li>Portfolio</li><li>Services</li><li>Team &amp; Experience</li><li>Contacts</li></ul>
  </div>

  <div class="footer-col col-news">
    <h3>Sign up for Newsletter</h3>
    <p>Sign up to our mailing list</p>
    <div class="email-field">Enter email</div>
    <div class="subscribe">Subscribe</div>
  </div>

  <div class="footer-rule"></div>
  <p class="copyright">Copyrights © 2019 | All Rights Reserved | Disclaimer</p>
</footer>

</body>
</html>
```